Harlow Mechanical Contractors needs a Website

Create basic website for commercial plumbing and mechanical contractor; to include pictures of works in progress and completed works, description of all services offered and geographical locations and licenses

Target Market(s)

General Contractors, Real Estate Developers, Construction Companies

Industry/Entity Type

Construction

Coding

Coded - Design and coding required

Number of Pages Required

5+ page

• See logo attached to project

Colors
0392cd

```html
<!DOCTYPE html>
<html lang="en">
<head>
<meta charset="utf-8">
<title>Harlow Mechanical Contractors</title>
<link href="https://fonts.googleapis.com/css2?family=Open+Sans:wght@400;600;700&family=Raleway:wght@400;600;700;800&display=swap" rel="stylesheet">
<style>
:root{
  --brand:#0392cd;
  --brand-dark:#0a7fb6;
  --navy:#1c4a6e;
  --ink:#3d3d3d;
  --heading:#454545;
  --muted:#7a7a7a;
  --orange:#f39200;
  --white:#ffffff;
  --footer-bar:#e9e9e9;
  --band:#163a4d;
}
*{margin:0;padding:0;box-sizing:border-box}
html,body{width:1200px;height:2510px;overflow:hidden;background:var(--white)}
body{position:relative;font-family:"Open Sans",Arial,sans-serif;color:var(--ink)}
.abs{position:absolute}

/* header */
.site-header{position:absolute;left:0;top:0;width:1200px;height:84px;background:var(--white);box-shadow:0 1px 4px rgba(0,0,0,.08);z-index:2}
.brand{position:absolute;display:flex;align-items:center;gap:8px}
.brand-dot{width:30px;height:30px;border-radius:50%;background:var(--navy);flex:none}
.brand-name{font-family:"Raleway",Arial,sans-serif;font-weight:800;color:var(--navy);text-transform:uppercase;line-height:1.05}
.site-header .brand{left:100px;top:18px}
.site-header .brand-name{font-size:12px}
.main-nav{position:absolute;top:34px;left:0;font-size:13px;color:#333}
.main-nav a{position:absolute;white-space:nowrap;color:#333;text-decoration:none}
.main-nav .caret{display:inline-block;width:6px;height:6px;border-right:1.5px solid #555;border-bottom:1.5px solid #555;transform:rotate(45deg);margin-left:9px;position:relative;top:-3px}
.call{position:absolute;left:954px;top:22px;display:flex;align-items:center;gap:12px}
.call-icon{width:38px;height:38px;border-radius:50%;background:var(--brand);display:flex;align-items:center;justify-content:center}
.call-text{font-size:12px;line-height:1.45;color:#222}
.call-text strong{display:block;color:var(--orange);font-weight:600;font-size:13px}

/* hero */
.hero{position:absolute;left:0;top:84px;width:1200px;height:505px}
.hero-photo{position:absolute;inset:0;background:linear-gradient(90deg,#eef0f1 0%,#e4e6e7 40%,#c9d2dc 62%,#6d87a8 78%,#c7ccd0 100%)}
.hero-title{position:absolute;left:100px;top:136px;font-family:"Raleway",Arial,sans-serif;font-weight:800;color:var(--navy);font-size:54px;line-height:1}
.hero-sub{position:absolute;left:100px;top:197px;font-family:"Raleway",Arial,sans-serif;font-weight:800;color:var(--brand);font-size:33px;line-height:1}
.hero-text{position:absolute;left:100px;top:244px;width:470px;font-size:19px;line-height:1.55;color:#2a2a2a}
.btn{position:absolute;left:100px;top:323px;width:165px;height:47px;background:var(--brand);color:var(--white);font-size:13px;font-weight:700;text-transform:uppercase;display:flex;align-items:center;justify-content:center;border-radius:2px;box-shadow:0 2px 4px rgba(0,0,0,.2)}
.dots{position:absolute;display:flex;gap:6px}
.dots span{width:8px;height:8px;border-radius:50%;background:#bbb}
.dots span.on{background:var(--brand)}
.hero .dots{left:575px;top:479px}

/* welcome */
.welcome-top{position:absolute;left:0;top:660px;width:1200px;text-align:center;font-family:"Raleway",Arial,sans-serif;font-size:30px;color:var(--heading);font-weight:400}
.welcome-title{position:absolute;left:0;top:702px;width:1200px;text-align:center;font-family:"Raleway",Arial,sans-serif;font-size:30px;font-weight:700;color:var(--heading)}
.welcome-text{position:absolute;left:155px;top:766px;width:890px;text-align:center;font-size:12.5px;line-height:1.85;color:var(--muted)}

/* how it works */
.how{position:absolute;left:100px;top:932px;width:1001px;height:340px;display:flex}
.video{position:relative;width:501px;height:340px}
.video-still{position:absolute;left:0;top:0;width:501px;height:310px;background:linear-gradient(120deg,#2b3034 0%,#6d7378 35%,#9aa0a3 50%,#5a5f5f 70%,#2c2f30 100%)}
.play{position:absolute;left:219px;top:124px}
.video-bar{position:absolute;left:0;top:310px;width:501px;height:30px;background:#0d0d0d}
.how-panel{width:500px;height:340px;background:var(--brand);color:var(--white);padding:84px 72px 0 72px}
.how-panel h2{font-family:"Raleway",Arial,sans-serif;font-weight:700;font-size:29px;margin-bottom:16px}
.how-panel p{font-size:13px;line-height:1.95}

/* services */
.services-title{position:absolute;left:0;top:1337px;width:1200px;text-align:center;font-family:"Raleway",Arial,sans-serif;font-weight:700;font-size:31px;color:var(--heading)}
.services-sub{position:absolute;left:0;top:1385px;width:1200px;text-align:center;font-size:12.5px;color:var(--muted)}
.service{position:absolute;top:1448px;width:324px}
.service-photo{width:324px;height:204px}
.service-name{margin-top:17px;text-align:center;font-size:13px;font-weight:700;color:#222;text-transform:uppercase}

/* testimonial */
.testimonial{position:absolute;left:0;top:1761px;width:1200px;height:457px}
.testimonial-bg{position:absolute;inset:0;background:radial-gradient(ellipse at 70% 40%,#2c5870 0%,#1d455b 45%,#132f40 100%)}
.quote-mark{position:absolute;left:584px;top:90px;font-family:"Raleway",Arial,sans-serif;font-weight:800;font-size:58px;line-height:1;color:var(--white)}
.testimonial-text{position:absolute;left:170px;top:144px;width:860px;text-align:center;font-size:14px;line-height:2.1;color:var(--white)}
.avatar{position:absolute;left:553px;top:226px;width:94px;height:94px;border-radius:50%;border:4px solid var(--white);background:linear-gradient(160deg,#c9d7e4,#8aa2b8)}
.author{position:absolute;left:0;top:342px;width:1200px;text-align:center;color:var(--white);font-size:13px}
.author strong{font-weight:700}
.testimonial .dots{left:585px;top:387px}
.testimonial .dots span{width:7px;height:7px;background:#5d7d90}
.testimonial .dots span.on{background:var(--brand)}

/* footer */
.site-footer{position:absolute;left:0;top:2218px;width:1200px;height:248px}
.site-footer .brand{left:100px;top:80px;gap:12px}
.site-footer .brand-dot{width:40px;height:40px}
.site-footer .brand-name{font-size:16px}
.footer-col{position:absolute;top:44px;font-size:11.5px;color:#555}
.footer-col h3{font-family:"Open Sans",Arial,sans-serif;font-size:14px;font-weight:700;color:var(--brand);margin-bottom:14px}
.footer-col ul{list-style:none}
.footer-col li{line-height:23px}
.contact-line{display:flex;align-items:center;gap:10px;line-height:25px}
.contact-line.plain{padding-left:0}
.social{display:flex;gap:8px;margin-top:14px}
.social span{width:34px;height:34px;border-radius:50%}
.footer-bar{position:absolute;left:0;top:2466px;width:1200px;height:44px;background:var(--footer-bar);text-align:center;line-height:44px;font-size:11.5px;color:#777}
</style>
</head>
<body>

<header class="site-header">
  <div class="brand">
    <span class="brand-dot"></span>
    <span class="brand-name">Harlow<br>Mechanical<br>Contractors</span>
  </div>
  <nav class="main-nav">
    <a style="left:424px">Home</a>
    <a style="left:516px">About Us</a>
    <a style="left:626px">Services<span class="caret"></span></a>
    <a style="left:732px">Testimonials</a>
    <a style="left:860px">Contact us</a>
  </nav>
  <div class="call">
    <span class="call-icon">
      <svg width="18" height="18" viewBox="0 0 24 24"><path fill="#fff" d="M6.6 10.8a15.2 15.2 0 0 0 6.6 6.6l2.2-2.2c.3-.3.7-.4 1-.2 1.1.4 2.3.6 3.6.6.6 0 1 .4 1 1V20c0 .6-.4 1-1 1A17 17 0 0 1 3 4c0-.6.4-1 1-1h3.5c.6 0 1 .4 1 1 0 1.3.2 2.5.6 3.6.1.3 0 .7-.2 1z"/></svg>
    </span>
    <div class="call-text">Call us :<strong>(0555) 010 442</strong></div>
  </div>
</header>

<section class="hero">
  <div class="hero-photo" role="img" aria-label="Photo of a plumber in a kitchen holding a wrench, tap and hoses"></div>
  <h1 class="hero-title">HARLOW</h1>
  <div class="hero-sub">MECHANICAL CONTRACTORS</div>
  <p class="hero-text">We install full plumbing services for large offices, condominiums, and industrial projects.</p>
  <a class="btn">Contact here!</a>
  <div class="dots"><span class="on"></span><span></span><span></span><span></span></div>
</section>

<section>
  <div class="welcome-top">WELCOME TO</div>
  <h2 class="welcome-title">HARLOW MECHANICAL CONTRACTORS</h2>
  <p class="welcome-text">Lorem Ipsum is simply dummy text of the printing and typesetting industry. Lorem Ipsum has been the industry's standard dummy text ever since the 1500s, when an unknown printer took a galley of type and scrambled it to make a type specimen book. It has survived not only five centuries, but also the leap into electronic typesetting, remaining essentially unchanged. It was popularised in the 1960s with the release of Letraset sheets containing Lorem Ipsum passages, and more recently with desktop publishing software...</p>
</section>

<section class="how">
  <div class="video">
    <div class="video-still" role="img" aria-label="Video still of an industrial plant room with pipework and control panels"></div>
    <svg class="play" width="64" height="64" viewBox="0 0 64 64"><circle cx="32" cy="32" r="32" fill="#e8534e"/><path d="M25 19 L47 32 L25 45 Z" fill="#fff"/></svg>
    <div class="video-bar">
      <svg width="501" height="30" viewBox="0 0 501 30">
        <rect x="8" y="10" width="3" height="10" fill="#fff"/><rect x="14" y="10" width="3" height="10" fill="#fff"/>
        <path d="M32 12h4l5-4v14l-5-4h-4z" fill="#fff"/>
        <line x1="52" y1="4" x2="52" y2="26" stroke="#333"/>
        <text x="425" y="19" font-size="8" fill="#ccc" font-family="Open Sans, sans-serif">10:11 / 11:30</text>
        <path d="M483 9h-4v4M490 9h4v4M483 22h-4v-4M490 22h4v-4" stroke="#fff" stroke-width="1.6" fill="none"/>
      </svg>
    </div>
  </div>
  <div class="how-panel">
    <h2>HOW IT WORKS</h2>
    <p>Lorem Ipsum is simply dummy text of the printing and typesetting industry. Lorem Ipsum has been the industry's standard dummy text ever since the 1500s, when an unknown printer took a galley of type and scrambled it to make a type specimen book. It has survived not only five centuries...</p>
  </div>
</section>

<section>
  <h2 class="services-title">OUR SERVICES</h2>
  <p class="services-sub">Lorem Ipsum is simply dummy text of the printing and typesetting industry. Lorem Ipsum has been the industry's standard dummy</p>
  <div class="service" style="left:100px">
    <div class="service-photo" role="img" aria-label="Photo of office project managers in hard hats" style="background:linear-gradient(135deg,#c5d6e6 0%,#8fa9c4 45%,#3d5578 100%)"></div>
    <div class="service-name">Large offices</div>
  </div>
  <div class="service" style="left:439px">
    <div class="service-photo" role="img" aria-label="Photo of a plumber fitting pipes under a sink" style="background:linear-gradient(135deg,#d9d2c8 0%,#9c8370 50%,#4f3a2e 100%)"></div>
    <div class="service-name">Condominiums</div>
  </div>
  <div class="service" style="left:777px">
    <div class="service-photo" role="img" aria-label="Photo of a worker in a hard hat adjusting industrial valves" style="background:linear-gradient(135deg,#6b6150 0%,#b59a5e 40%,#2f4a7a 75%,#4a4f55 100%)"></div>
    <div class="service-name">Industrial projects</div>
  </div>
</section>

<section class="testimonial">
  <div class="testimonial-bg" role="img" aria-label="Background photo of plumbing fittings and flexible hoses"></div>
  <div class="quote-mark">&ldquo;</div>
  <p class="testimonial-text">Lorem Ipsum is simply dummy text of the printing and typesetting industry. Lorem Ipsum has been the industry's standard dummy text ever since the 1500s, when an unknown printer took a galley of type and scrambled it to make a type specimen book</p>
  <div class="avatar" role="img" aria-label="Portrait of the client"></div>
  <div class="author"><strong>- Nolan Brecker -</strong> Business man</div>
  <div class="dots"><span class="on"></span><span></span><span></span></div>
</section>

<footer class="site-footer">
  <div class="brand">
    <span class="brand-dot"></span>
    <span class="brand-name">Harlow<br>Mechanical<br>Contractors</span>
  </div>
  <div class="footer-col" style="left:350px">
    <h3>Harlow Mechanical Contractors</h3>
    <div class="contact-line">48 Foundry Lane, Eastbrook,</div>
    <div class="contact-line">Region code : 4412078</div>
    <div class="contact-line" style="margin-top:6px">
      <svg width="11" height="11" viewBox="0 0 24 24"><path fill="#0392cd" d="M6.6 10.8a15.2 15.2 0 0 0 6.6 6.6l2.2-2.2c.3-.3.7-.4 1-.2 1.1.4 2.3.6 3.6.6.6 0 1 .4 1 1V20c0 .6-.4 1-1 1A17 17 0 0 1 3 4c0-.6.4-1 1-1h3.5c.6 0 1 .4 1 1 0 1.3.2 2.5.6 3.6.1.3 0 .7-.2 1z"/></svg>
      (0555) 010 442</div>
    <div class="contact-line">
      <svg width="11" height="9" viewBox="0 0 22 16"><rect width="22" height="16" rx="2" fill="#0392cd"/><path d="M1 2l10 7 10-7" stroke="#fff" stroke-width="1.8" fill="none"/></svg>
      info@harlowmechanical.example</div>
  </div>
  <div class="footer-col" style="left:651px">
    <h3>Welcome</h3>
    <ul><li>Home</li><li>About us</li><li>Services</li><li>Blog</li><li>Testimonials</li><li>Contact us</li></ul>
  </div>
  <div class="footer-col" style="left:778px">
    <h3>Information</h3>
    <ul><li>Terms &amp; Conditions</li><li>Privacy policy</li><li>Disclaimer</li><li>Sitemap</li></ul>
  </div>
  <div class="footer-col" style="left:934px">
    <h3>Social media</h3>
    <div>Connect with our social network</div>
    <div class="social">
      <span style="background:#3b5998"></span>
      <span style="background:#2fa9e0"></span>
      <span style="background:#d9262a"></span>
      <span style="background:#1f6e8c"></span>
    </div>
  </div>
</footer>
<div class="footer-bar">Copyright &copy; Harlow Mechanical Contractors. 2016.All rights reserved.</div>

</body>
</html>
```